We need a new business card that reflects who we are. Professional, classy, modern, and service ori

We need a business card design for a window coverings design company in Kansas City called Bright Lane Interiors. We offer professional, modern, and high quality window covering products. We are looking to portray an image of a big, national franchise. We are a 5 location (with showrooms) business with 10 professional designers and 4 professional installers. These cards will be used with Thank you cards, given to realtors, and asked for referrals with.

Target Market(s)

Kansas City

Industry/Entity Type

Business

Contact Information for Business Card

We would like our card to look clean and simple on the front, featuring our logo and Marlow Fenwick's. Our designers' phone numbers and emails should be displayed as well as their title.

Font styles to use
Sans Serif

Colors

Designer to choose colors to be used in the design.

Requirements
Must have
• Front - Logos, name, phone number, email address
• Back - Showroom locations, social media? Appt date/time?
Nice to have
• I would like a clean and modern look (not contemporary. I like a white background, but I am open to ideas. Looking for a "National chain" look for a small business.
Should not have
• Too much busyness.

```html
<!DOCTYPE html>
<html lang="en">
<head>
<meta charset="utf-8">
<title>Bright Lane Interiors – Business Card</title>
<link rel="stylesheet" href="https://fonts.googleapis.com/css2?family=Lato:wght@400;700&family=Tinos:wght@400;700&display=swap">
<style>
  :root {
    --stage: #555555;
    --card: #ffffff;
    --brand-red: #c64245;
    --brand-grey: #8e9194;
    --ink: #1a1a1a;
    --rule: #9a9a9a;
    --band: #000000;
    --social: #1f8fc8;
    --partner-orange: #f0861e;
    --partner-slate: #56636e;
  }
  * { margin: 0; padding: 0; box-sizing: border-box; }
  html, body { width: 1200px; height: 900px; overflow: hidden; }
  body { background: var(--stage); position: relative; font-family: "Lato", sans-serif; color: var(--ink); }

  .card {
    position: absolute; top: 170px; width: 347px; height: 561px;
    background: var(--card); overflow: hidden;
    box-shadow: 3px 4px 6px rgba(0,0,0,0.45);
  }
  .card--front { left: 259px; }
  .card--back { left: 631px; }

  .centered { position: absolute; left: 0; width: 100%; text-align: center; }

  /* Front */
  .brand-mark { position: absolute; left: 143px; top: 95px; width: 60px; height: 60px; background: var(--brand-red); }
  .brand-name { top: 168px; font-family: "Tinos", serif; font-size: 24px; font-weight: 400; color: var(--ink); }
  .brand-tagline { top: 198px; font-family: "Tinos", serif; font-size: 13.5px; color: var(--ink); }

  .person-name { top: 274px; font-family: "Tinos", serif; font-size: 20px; font-weight: 700; letter-spacing: 0.5px; color: var(--ink); }
  .person-name .first { color: var(--brand-red); }
  .person-title { top: 299px; font-size: 15px; }
  .rule { position: absolute; left: 82px; width: 182px; height: 1px; background: var(--rule); }
  .rule--top { top: 329px; }
  .rule--bottom { top: 400px; }
  .contact { font-size: 15px; }
  .contact--phone { top: 342px; }
  .contact--email { top: 363px; }
  .contact .label { color: var(--brand-red); }

  .social-band { position: absolute; left: 129px; top: 431px; width: 218px; height: 38px; background: var(--band); border-radius: 19px 0 0 19px; }
  .social-dot { position: absolute; top: 7px; width: 24px; height: 24px; border-radius: 50%; background: var(--social); }
  .social-dot:nth-child(1) { left: 20px; }
  .social-dot:nth-child(2) { left: 48px; }
  .social-dot:nth-child(3) { left: 76px; }
  .social-dot:nth-child(4) { left: 105px; }

  .partner-mark { position: absolute; left: 47px; top: 417px; width: 70px; height: 70px; border-radius: 50%; background: var(--partner-orange); }
  .partner-name { position: absolute; left: 20px; width: 126px; top: 494px; text-align: center; font-size: 15px; font-weight: 700; line-height: 1.15; color: var(--partner-slate); }

  /* Back */
  .back-header { position: absolute; left: 0; top: 0; width: 100%; height: 173px; background: var(--brand-red); }
  .back-brand { top: 70px; font-family: "Tinos", serif; font-size: 30px; font-weight: 400; color: var(--ink); }
  .locations { position: absolute; left: 0; top: 178px; width: 100%; height: 199px; background: var(--brand-grey); color: #fff; text-align: center; }
  .locations h2 { margin-top: 30px; font-size: 18px; font-weight: 400; letter-spacing: 0.3px; }
  .locations ul { list-style: none; font-size: 15px; line-height: 23px; }

  .appointment-title { top: 412px; font-size: 18px; font-weight: 400; color: var(--brand-red); }
  .appointment-field { position: absolute; left: 40px; width: 267px; display: flex; align-items: flex-end; font-size: 17px; }
  .appointment-field--date { top: 464px; }
  .appointment-field--time { top: 498px; }
  .appointment-field .line { flex: 1; margin-left: 4px; margin-bottom: 7px; height: 1px; background: var(--rule); }
</style>
</head>
<body>
  <section class="card card--front" aria-label="Business card front">
    <div class="brand-mark"></div>
    <p class="centered brand-name">Bright Lane Interiors</p>
    <p class="centered brand-tagline">Blinds, Shades, Shutters, Draperies &amp; Decor</p>

    <p class="centered person-name"><span class="first">DANIEL</span> HAYES</p>
    <p class="centered person-title">Managing Director</p>
    <div class="rule rule--top"></div>
    <p class="centered contact contact--phone"><span class="label">P:</span> 444 555 0142</p>
    <p class="centered contact contact--email"><span class="label">E:</span> info@brightlaneinteriors.com</p>
    <div class="rule rule--bottom"></div>

    <div class="social-band" aria-label="Social media">
      <span class="social-dot"></span><span class="social-dot"></span><span class="social-dot"></span><span class="social-dot"></span>
    </div>
    <div class="partner-mark"></div>
    <p class="partner-name">Marlow Fenwick Gallery</p>
  </section>

  <section class="card card--back" aria-label="Business card back">
    <div class="back-header"></div>
    <p class="centered back-brand">Bright Lane Interiors</p>
    <div class="locations">
      <h2>SHOWROOM LOCATIONS</h2>
      <ul>
        <li>LOCATION 1</li>
        <li>LOCATION 2</li>
        <li>LOCATION 3</li>
        <li>LOCATION 4</li>
        <li>LOCATION 5</li>
      </ul>
    </div>
    <p class="centered appointment-title">NEXT APPOINTMENT</p>
    <div class="appointment-field appointment-field--date"><span>DATE</span><span class="line"></span></div>
    <div class="appointment-field appointment-field--time"><span>TIME</span><span class="line"></span></div>
  </section>
</body>
</html>
```